Business cards and stationary design

We just completed the design of our new logo and we need to print new business cards and letterhead for our nonprofit. We are looking for a fresh new design that shows off our new logo. On letterhead, we must have a column on the right or left to include our Board of Directors (up to 45 names) (see attachment)

Industry/Entity Type

Non-Profit

Contact Information for Business Card

Standard business card with name, title, Company name, mailing address phone numbers, email address and website. Tagline on back "Bringing the homeless home"

Font styles to use
Sans Serif

Requirements
Must have
• include pertinent information above
• new logo
• fonts compatible with logo
• should use logo colors only
Nice to have
• tag lines

```html
<!DOCTYPE html>
<html lang="en">
<head>
<meta charset="utf-8">
<title>Homeward Haven Center – Business Card</title>
<link rel="stylesheet" href="https://fonts.googleapis.com/css2?family=Roboto:wght@400;500;700&family=Roboto+Condensed:wght@500;700&display=swap">
<style>
  :root {
    --backdrop: #2b2b2b;
    --brand-red: #d62027;
    --brand-teal: #0585a6;
    --brand-yellow: #f4b71f;
    --paper: #f1f1f1;
    --white: #ffffff;
    --card-shadow: rgba(0, 0, 0, 0.55);
  }
  * { margin: 0; padding: 0; box-sizing: border-box; }
  html, body {
    width: 1200px;
    height: 960px;
    overflow: hidden;
    background: var(--backdrop);
    font-family: "Roboto", Arial, sans-serif;
  }
  .canvas { position: relative; width: 1200px; height: 960px; }

  .card {
    position: absolute;
    left: 320px;
    width: 600px;
    box-shadow: 0 6px 14px var(--card-shadow);
  }

  /* Back side */
  .card-back {
    top: 100px;
    height: 346px;
    background: var(--brand-red);
    color: var(--white);
    display: flex;
    flex-direction: column;
    align-items: center;
  }
  .card-back .brand-mark {
    margin-top: 150px;
    display: flex;
    align-items: center;
    gap: 14px;
    font-size: 34px;
    font-weight: 700;
    letter-spacing: 2px;
    text-transform: uppercase;
  }
  .card-back .brand-mark .dot {
    width: 22px; height: 22px;
    background: var(--white);
  }
  .card-back .web {
    margin-top: auto;
    margin-bottom: 30px;
    font-size: 14px;
    letter-spacing: 4.6px;
  }

  /* Front side */
  .card-front {
    top: 493px;
    height: 342px;
    display: flex;
    background: var(--paper);
  }
  .contact-panel {
    width: 265px;
    background: var(--brand-teal);
    color: var(--white);
    padding: 74px 0 0 32px;
  }
  .person-name {
    font-family: "Roboto Condensed", Arial, sans-serif;
    font-size: 23px;
    font-weight: 700;
    line-height: 1.1;
  }
  .person-title {
    font-size: 14px;
    font-weight: 500;
    margin-top: 6px;
  }
  .address {
    margin-top: 28px;
    font-size: 14px;
    line-height: 18px;
  }
  .address .org { font-weight: 500; }
  .contact-list {
    list-style: none;
    margin-top: 12px;
    font-size: 14px;
    line-height: 19px;
  }
  .contact-list li { display: flex; align-items: center; gap: 8px; }
  .contact-list svg { width: 13px; height: 13px; fill: var(--white); flex: none; }

  .logo-panel {
    flex: 1;
    display: flex;
    align-items: center;
    justify-content: center;
  }
  .brand-lockup {
    display: flex;
    flex-direction: column;
    align-items: center;
    margin-top: 36px;
    color: var(--brand-teal);
    font-size: 19px;
    font-weight: 500;
    letter-spacing: 2px;
    text-transform: uppercase;
  }
  .brand-lockup .rule {
    width: 248px;
    height: 1px;
    margin-top: 8px;
    background: var(--brand-red);
  }
  .accent-strip { width: 19px; background: var(--brand-yellow); }
</style>
</head>
<body>
<main class="canvas">
  <section class="card card-back" aria-label="Business card back">
    <div class="brand-mark"><span class="dot"></span>Homeward Haven</div>
    <div class="web">www.homewardhaven.org</div>
  </section>

  <section class="card card-front" aria-label="Business card front">
    <div class="contact-panel">
      <h1 class="person-name">DANIEL PORTER</h1>
      <p class="person-title">CEO/FOUNDER</p>
      <address class="address">
        <span class="org">Homeward Haven Center</span><br>
        2914 Aspen Ridge Lane<br>
        Fairbanks, Alaska 99701
      </address>
      <ul class="contact-list">
        <li>
          <svg viewBox="0 0 24 24" aria-hidden="true"><path d="M6.6 10.8a15.1 15.1 0 0 0 6.6 6.6l2.2-2.2c.3-.3.7-.4 1-.2 1.1.4 2.3.6 3.6.6.6 0 1 .4 1 1V20c0 .6-.4 1-1 1A17 17 0 0 1 3 4c0-.6.4-1 1-1h3.5c.6 0 1 .4 1 1 0 1.3.2 2.5.6 3.6.1.3 0 .7-.2 1z"/></svg>
          555 014 2781
        </li>
        <li>
          <svg viewBox="0 0 24 24" aria-hidden="true"><path d="M2 5h20v14H2z M2 5l10 8 10-8" fill="none" stroke="#fff" stroke-width="2"/></svg>
          daniel@homewardhaven.org
        </li>
        <li>
          <svg viewBox="0 0 24 24" aria-hidden="true"><circle cx="12" cy="12" r="10"/><path d="M2 12h20M12 2c3 3 3 17 0 20M12 2c-3 3-3 17 0 20" fill="none" stroke="#0585a6" stroke-width="1.6"/></svg>
          www.homewardhaven.org
        </li>
      </ul>
    </div>
    <div class="logo-panel">
      <div class="brand-lockup">
        Homeward Haven Center
        <span class="rule"></span>
      </div>
    </div>
    <div class="accent-strip"></div>
  </section>
</main>
</body>
</html>
```